Progressive European Honey Business needs minimalistic packaging design

Hello - thank you for your interest in our brief. We are Honey Plinks, a London based Honey business, importing only the best honey Europe has to offer. Our values are deeply rooted with in progressive liberal values and we are looking for minimalist packaging, which reflects that.

We are looking for a design, which dimensions fit with our packaging option (Vessio Glass Jar | HEIGHT 90mm | DIAMETER 63mm). We will require a various output files (High Resolution JPEG (CMYK Colors 300 dpi) Source File Ai, PSD, PDF, Printing files (die cut, die folding) and a 3D Mockup of the packaging for use within digital commerce platforms.

We must be able to adjust the free text on the label front and it should include the following:
Brand Name
Honey type
Limited edition No. X / 100 ( X being the number of purchase i.e. 25 / 100)
EU Honey, Single Orgin (Germany)
(c) The net weight (250g)

The back must include room for additional information (again adjustable by us) and the following:
“Unsuitable for children under 12 months”
(b) The appropriate durability declaration

In total, we are looking for
a) A front label
b) A back label
c) A seal (round) including the attached bee and logo included in the Zip file.
Do note that a) & b) can also be combined into one design as long as the symmetry on the jar stays intact.

The final design should communicate modern aesthetics, high quality, that are slightly provocative and pop off the shelves.

Hi folks, sorry for the delay in completing this project, but my business partner had a leak in his house. We planned to finalise our review today, but this will have to wait until it's no longer raining in his livingroom. Our sincere apologies!

• See branding guidelines

• Must follow the branding guideline and fonts provided as attachment

```html
<!DOCTYPE html>
<html lang="en">
<head>
<meta charset="utf-8">
<title>Honey Plinks – Lavender Honey Label</title>
<link rel="stylesheet" href="https://fonts.googleapis.com/css2?family=Jost:wght@300;400;500&family=Playfair+Display:wght@900&display=swap">
<style>
  :root {
    --page: #e9e9e9;
    --label-plum: #3a2536;
    --label-plum-light: #4a3245;
    --band: #f2f2f4;
    --lavender-deep: #8a3f9e;
    --lavender-light: #d08fd6;
    --sky: #c9c5d8;
    --seal: #f7e53a;
    --seal-ink: #2a1a26;
    --rule: #d8c53a;
    --ink: #ffffff;
  }
  * { margin: 0; padding: 0; box-sizing: border-box; }
  html, body { width: 1200px; height: 960px; overflow: hidden; background: var(--page); }
  .label {
    position: absolute; left: 80px; top: 270px; width: 1040px; height: 420px;
    background: linear-gradient(180deg, var(--label-plum-light), var(--label-plum));
    overflow: hidden; border-radius: 4px;
  }
  .label-band { position: absolute; left: 0; top: 0; width: 100%; height: 38px; background: var(--band); }
  .label-art { position: absolute; left: 0; top: 0; }
  .back-panel { position: absolute; left: 40px; top: 80px; width: 260px; color: var(--ink); font-family: 'Jost', sans-serif; }
  .back-heading { font-weight: 500; font-size: 20px; letter-spacing: 1px; margin-bottom: 14px; }
  .back-copy { font-weight: 300; font-size: 14px; line-height: 1.7; }
  .edition-seal {
    position: absolute; left: 375px; top: 205px; width: 104px; height: 104px; border-radius: 50%;
    background: var(--seal); color: var(--seal-ink); display: flex; flex-direction: column;
    align-items: center; justify-content: center; transform: rotate(-20deg);
    font-family: 'Playfair Display', serif; font-weight: 900; font-size: 13px; line-height: 1.15; text-align: center;
  }
  .brand-name {
    position: absolute; left: 503px; top: 208px; color: var(--ink);
    font-family: 'Jost', sans-serif; font-weight: 500; font-size: 58px; line-height: 1; letter-spacing: 2px;
  }
  .honey-type {
    position: absolute; left: 505px; top: 292px; color: var(--ink);
    font-family: 'Jost', sans-serif; font-weight: 500; font-size: 24px; letter-spacing: 7px;
  }
  .origin {
    position: absolute; left: 505px; top: 332px; color: var(--ink);
    font-family: 'Jost', sans-serif; font-weight: 300; font-size: 19px;
  }
  .net-weight {
    position: absolute; right: 40px; top: 346px; color: var(--ink);
    font-family: 'Jost', sans-serif; font-weight: 400; font-size: 20px;
  }
  .weight-rule { position: absolute; left: 360px; right: 30px; top: 376px; height: 2px; background: var(--rule); }
</style>
</head>
<body>
  <main class="label">
    <div class="label-band"></div>
    <svg class="label-art" width="1040" height="420" viewBox="0 0 1040 420">
      <defs>
        <linearGradient id="lavender-field" x1="0" y1="0" x2="1" y2="1">
          <stop offset="0" stop-color="#c9c5d8"/>
          <stop offset="0.3" stop-color="#d08fd6"/>
          <stop offset="1" stop-color="#8a3f9e"/>
        </linearGradient>
      </defs>
      <path role="img" aria-label="Photograph of a lavender field in rows"
        d="M340 38 H760 C740 70 700 60 690 95 C680 130 630 120 600 130 C560 145 520 135 480 150 C440 165 420 190 400 230 C390 260 380 300 360 320 L340 330 Z"
        fill="url(#lavender-field)"/>
    </svg>

    <section class="back-panel">
      <h2 class="back-heading">Tasting Notes</h2>
      <p class="back-copy">Floral, bright and gently sweet.<br>Harvested from summer lavender<br>fields and cold packed by hand.<br>Unsuitable for children under<br>12 months. Best before: see lid.</p>
    </section>

    <div class="edition-seal"><span>LIMITED</span><span>EDITION</span><span>NO. X / 100</span></div>
    <h1 class="brand-name">Honey Plinks</h1>
    <p class="honey-type">LAVENDER HONEY</p>
    <p class="origin">EU Honey ● Single Orgin (Germany)</p>
    <p class="net-weight">250g</p>
    <div class="weight-rule"></div>
  </main>
</body>
</html>
```